Basic business card

use my newly created logo - and the phrases (Faster Yield Ramp & Smarter Wafer Validation for Every Launch) - and my new email domain / ID - use at conferences / tradeshows

Industry/Entity Type

semiconductor

Contact Information for Business Card

Daniel K Forde, Owner, communicate via Logo - Lower COT - Cost of Test, Accelerated NPI - New Product Introduction, phone +1 555 613 0946, Chandler, Arizona, USA, daniel.forde@qal-vub.com

Font styles to use
Sans Serif

Requirements
Nice to have
• re-use my logo created via Pixel Harbor last August (#7315926)

```html
<!DOCTYPE html>
<html lang="en">
<head>
<meta charset="utf-8">
<title>QAL-VUB Business Card</title>
<link rel="stylesheet" href="https://fonts.googleapis.com/css2?family=Montserrat:wght@400;500;700&display=swap">
<style>
  :root {
    --backdrop: #1f1f21;
    --navy: #4b5a76;
    --navy-ink: #3f4d69;
    --paper: #ffffff;
    --text-grey: #3c3f47;
    --rule: #5b6a86;
    --orange: #f08a1c;
    --blue: #1e78c8;
    --green: #7cbf2a;
  }
  * { box-sizing: border-box; margin: 0; padding: 0; }
  html, body { width: 1200px; height: 988px; overflow: hidden; }
  body {
    background: var(--backdrop);
    font-family: "Montserrat", sans-serif;
    position: relative;
  }
  .card {
    position: absolute;
    width: 600px;
    height: 343px;
    border-radius: 22px;
    box-shadow: 0 10px 30px rgba(0,0,0,.45);
    overflow: hidden;
  }
  .card-front { left: 70px; top: 90px; background: var(--navy); color: var(--paper); }
  .card-back { left: 530px; top: 555px; background: var(--paper); }

  .brand { display: flex; align-items: center; gap: 14px; font-weight: 500; letter-spacing: 2px; white-space: nowrap; }
  .brand-square { width: 22px; height: 22px; flex: none; }

  .card-front .brand {
    position: absolute; left: 0; right: 0; top: 120px;
    justify-content: center; font-size: 58px; color: var(--paper);
  }
  .card-front .brand-square { background: var(--paper); width: 30px; height: 30px; }
  .tagline {
    position: absolute; left: 20px; right: 20px; bottom: 52px;
    text-align: center; font-size: 14px; letter-spacing: 1.2px; font-weight: 400;
    white-space: nowrap;
  }

  .card-back .brand {
    position: absolute; left: 40px; top: 150px;
    font-size: 34px; color: var(--navy-ink);
  }
  .card-back .brand-square { background: var(--navy-ink); }
  .divider {
    position: absolute; left: 300px; top: 78px; width: 1px; height: 190px;
    background: var(--rule);
  }
  .contact { position: absolute; left: 328px; top: 88px; right: 20px; color: var(--text-grey); }
  .person-name { font-size: 24px; font-weight: 700; color: var(--navy-ink); white-space: nowrap; }
  .person-role { font-size: 14px; margin: 2px 0 20px; }
  .contact-list { list-style: none; font-size: 13.5px; }
  .contact-list li { display: flex; align-items: center; gap: 8px; margin-bottom: 9px; white-space: nowrap; }
  .contact-list svg { width: 14px; height: 14px; flex: none; }
</style>
</head>
<body>
  <section class="card card-front">
    <div class="brand"><span class="brand-square"></span>QAL-VUB</div>
    <p class="tagline">Faster Yield Ramp &amp; Smarter Wafer Validation for Every Launch</p>
  </section>

  <section class="card card-back">
    <div class="brand"><span class="brand-square"></span>QAL-VUB</div>
    <div class="divider"></div>
    <div class="contact">
      <h1 class="person-name">Daniel K Forde</h1>
      <p class="person-role">Owner</p>
      <ul class="contact-list">
        <li>
          <svg viewBox="0 0 16 16" aria-hidden="true"><path fill="var(--orange)" d="M3 2l3 0 1 4-2 1a9 9 0 0 0 4 4l1-2 4 1v3c0 1-1 1-2 1A12 12 0 0 1 2 4c0-1 0-2 1-2z"/></svg>
          +1 555 613 0946
        </li>
        <li>
          <svg viewBox="0 0 16 16" aria-hidden="true"><rect x="1" y="3" width="14" height="10" fill="var(--blue)"/><path d="M1 3l7 6 7-6" fill="none" stroke="#fff" stroke-width="1.4"/></svg>
          daniel.forde@qal-vub.com
        </li>
        <li>
          <svg viewBox="0 0 16 16" aria-hidden="true"><path fill="var(--green)" d="M8 1a5 5 0 0 1 5 5c0 4-5 9-5 9S3 10 3 6a5 5 0 0 1 5-5z"/><circle cx="8" cy="6" r="2" fill="#fff"/></svg>
          Brookvale , Nevada, USA
        </li>
      </ul>
    </div>
  </section>
</body>
</html>
```